New Business Card Design Project

I need a design for business cards, i am an electrical business called "Corvane Electrical and Communications" i need the cards to be double sided with the company logo on the back (attached) the front needs to say my company name, web site, email address, telephone number, and ABN number and electrical license number. I am open to different arrangements of the information but would like the background to be incorporating something electrical or something that looks smart. open to all additional ideas also.

The company colours are orange and grey see logo attached.

Business Name: Corvane Electrical and Communications
Website: corvaneelectricalandcomms.example.com.au
Email: brent@corvaneelectricalandcomms.example.com.au
Telephone(mobile): 0481209736
ABN: 71208349162
Lic No: 418273D

Target Market(s)

Business entities, Project Managers, Accounts, Clients

Industry/Entity Type

Electrician

Contact Information for Business Card

I need a design for business cards, i am an electrical business called "Corvane Electrical and Communications" i need the cards to be double sided with the company logo on the back (attached) the front needs to say my company name

Font styles to use
Serif
Sans Serif

Colors
f37122
5c5c5c

Requirements
Must have
• Must have the Logo on the back open to different ways of it being on the back but had in mind to keep it central but again open to other options
Nice to have
• A real modern cool background that is eye catching yet contemporary
Should not have
• No backgrounds of a light bulb or plug or anything like that

```html
<!DOCTYPE html>
<html lang="en">
<head>
<meta charset="utf-8">
<title>Corvane Electrical and Communications – Business Cards</title>
<link rel="stylesheet" href="https://fonts.googleapis.com/css2?family=Open+Sans:wght@400;600&display=swap">
<style>
  :root {
    --stage: #2b2b2b;
    --card: #050505;
    --orange: #f7a823;
    --brand-orange: #f37122;
    --grey: #5c5c5c;
    --white: #ffffff;
    --band: #f4f4f4;
  }
  * { margin: 0; padding: 0; box-sizing: border-box; }
  html, body {
    width: 1200px; height: 900px; overflow: hidden;
    background: var(--stage);
    font-family: "Open Sans", Arial, sans-serif;
  }
  .canvas {
    position: relative; width: 1200px; height: 900px;
  }
  .card {
    position: absolute; left: 250px; width: 700px; height: 400px;
    background: var(--card); border-radius: 22px; overflow: hidden;
  }
  .card--back { top: 40px; }
  .card--front { top: 460px; }

  .brand {
    position: absolute; left: 0; right: 0;
    display: flex; align-items: center; justify-content: center; gap: 16px;
  }
  .brand__dot {
    width: 22px; height: 22px; border-radius: 50%; background: var(--orange); flex: none;
  }
  .brand__name {
    color: var(--white); font-weight: 600; line-height: 1.05; text-align: left;
  }
  .brand__name .word { display: block; font-size: 64px; letter-spacing: 6px; text-transform: uppercase; }
  .brand__name .rest { display: block; font-size: 19px; letter-spacing: 1.5px; text-transform: uppercase; }

  .card--back .brand { top: 95px; }
  .web-band {
    position: absolute; left: 0; right: 0; top: 270px; height: 52px;
    background: var(--band);
    display: flex; align-items: center; justify-content: center;
    font-size: 21px; color: var(--grey);
  }
  .web-band .domain { color: var(--orange); }

  .holder { position: absolute; right: 34px; top: 30px; text-align: right; }
  .holder__name { color: var(--orange); font-size: 28px; letter-spacing: 0.5px; text-transform: uppercase; }
  .holder__role { color: var(--white); font-size: 13px; text-transform: uppercase; margin-top: -2px; }

  .card--front .brand { top: 115px; }
  .licence {
    position: absolute; left: 0; right: 0; top: 250px; text-align: center;
    font-size: 19px; color: var(--white);
  }
  .label { color: var(--orange); }
  .abn {
    position: absolute; right: 34px; top: 205px; font-size: 15px; color: var(--white);
  }
  .contacts {
    position: absolute; left: 34px; bottom: 28px; list-style: none;
    color: var(--white); font-size: 17px;
  }
  .contacts li { display: flex; align-items: center; gap: 12px; line-height: 26px; }
  .contacts svg { width: 15px; height: 15px; flex: none; fill: var(--orange); }
</style>
</head>
<body>
<main class="canvas">

  <section class="card card--back" aria-label="Card back">
    <div class="brand">
      <span class="brand__dot"></span>
      <div class="brand__name"><span class="word">Corvane</span><span class="rest">Electrical &amp; Communications</span></div>
    </div>
    <div class="web-band">www.<span class="domain">corvaneelectricalandcomms</span>.example.com.au</div>
  </section>

  <section class="card card--front" aria-label="Card front">
    <div class="holder">
      <div class="holder__name">Marlo Keating</div>
      <div class="holder__role">Director</div>
    </div>
    <div class="brand">
      <span class="brand__dot"></span>
      <div class="brand__name"><span class="word">Corvane</span><span class="rest">Electrical &amp; Communications</span></div>
    </div>
    <p class="licence"><span class="label">Lic No:</span> 418273D</p>
    <p class="abn"><span class="label">ABN:</span> 71208349162</p>
    <ul class="contacts">
      <li>
        <svg viewBox="0 0 16 16" aria-hidden="true"><path d="M3.5 1.5l2.5 0 1 3.5-1.8 1.2a8 8 0 0 0 4.6 4.6L11 9l3.5 1v2.5c0 1-1 2-2 2A11 11 0 0 1 1.5 3.5c0-1 1-2 2-2z"/></svg>
        0481-209-736
      </li>
      <li>
        <svg viewBox="0 0 16 16" aria-hidden="true"><path d="M1 3h14v10H1z M2.2 4.2v.3L8 9l5.8-4.5v-.3z" fill-rule="evenodd"/></svg>
        brent@corvaneelectricalandcomms.example.com.au
      </li>
      <li>
        <svg viewBox="0 0 16 16" aria-hidden="true"><path d="M8 1a7 7 0 1 0 0 14A7 7 0 0 0 8 1zm0 1.5c.8 0 1.8 1.9 2 4.5H6c.2-2.6 1.2-4.5 2-4.5zM2.6 7h2c.1-1.6.4-3 1-4a5.5 5.5 0 0 0-3 4zm8.8 0h2a5.5 5.5 0 0 0-3-4c.6 1 .9 2.4 1 4zM2.6 9a5.5 5.5 0 0 0 3 4c-.6-1-.9-2.4-1-4zm3.4 0c.2 2.6 1.2 4.5 2 4.5s1.8-1.9 2-4.5zm5.4 0c-.1 1.6-.4 3-1 4a5.5 5.5 0 0 0 3-4z"/></svg>
        www.corvaneelectricalandcomms.example.com.au
      </li>
    </ul>
  </section>

</main>
</body>
</html>
```